Waste management company seeks a new website design

We need a website design for an environmental services company called 'Laanemetsa Haldusgrupp.' We manage waste collection and recycling for 100K+ households and businesses across Estonia. Please use logos and colors from attached CVI file. The design should be extensively usable for our self-service portal and have a mobile-first approach as it will be turned into an app in the future. The new website should highlight our commitment to sustainability and provide easy access to our services with a clean, modern design. UX inspiration from https://ruvako.eu/et-ee/

```html
<!DOCTYPE html>
<html lang="et">
<head>
<meta charset="utf-8">
<title>Laanemetsa Haldusgrupp</title>
<link href="https://fonts.googleapis.com/css2?family=Poppins:wght@300;400;500;600;700;800&display=swap" rel="stylesheet">
<style>
:root{
  --green:#d3dc2c;
  --taupe:#aba39e;
  --brown:#7b6e68;
  --btn:#7d6e67;
  --ink:#4d4743;
  --muted:#8a817c;
  --card:#f4f2f0;
  --line:#e4e0dd;
  --white:#fff;
}
*{margin:0;padding:0;box-sizing:border-box}
html,body{width:1200px;height:4158px;overflow:hidden;background:var(--white);font-family:'Poppins',sans-serif;color:var(--ink)}
.page{position:relative;width:1200px;height:4158px}
.abs{position:absolute}

/* header */
.header{position:absolute;top:0;left:0;width:1200px;height:81px;background:var(--white)}
.brand{position:absolute;display:flex;align-items:center;gap:12px;font-weight:500;color:var(--brown)}
.brand .dot{width:40px;height:40px;border-radius:50%;background:var(--taupe)}
.header .brand{left:89px;top:20px;font-size:20px}
.nav{position:absolute;right:89px;top:21px;display:flex;align-items:center;gap:26px;font-size:11px;font-weight:500;color:var(--ink)}
.lang{display:flex;align-items:center;gap:6px}
.lang .flag{width:26px;height:26px;border-radius:50%;background:linear-gradient(#2a62b8 0 33%,#111 33% 66%,#fff 66%);border:1px solid var(--line)}
.btn-pill{background:var(--btn);color:var(--white);border-radius:20px;padding:12px 20px;font-weight:700;font-size:10.5px}
.burger{width:22px;display:flex;flex-direction:column;gap:5px}
.burger span{height:2px;background:var(--brown)}

/* hero */
.hero{position:absolute;top:81px;left:0;width:1200px;height:714px;overflow:hidden}
.hero-photo{position:absolute;inset:0;background:radial-gradient(circle at 78% 40%,#c9b59b 0,#a8835a 30%,#6b4a2c 65%,#3d2a1a 100%)}
.hero svg{position:absolute;left:0;top:0}
.hero-kicker{position:absolute;left:87px;top:168px;font-size:14px;color:#f1eeec;font-weight:500}
.hero-title{position:absolute;left:83px;top:196px;font-size:106px;line-height:1;font-weight:800;color:var(--white);letter-spacing:-2px}
.hero-sub{position:absolute;left:87px;top:340px;font-size:38px;font-weight:500;color:var(--white)}

/* quick links */
.quick{position:absolute;top:878px;left:0;width:1200px}
.quick-item{position:absolute;width:220px;text-align:center;font-size:15px;font-weight:600;color:var(--ink)}
.quick-item svg{display:block;margin:0 auto 12px}

/* about */
.round-photo{position:absolute;border-radius:50%;border:6px solid var(--white);box-shadow:0 18px 40px rgba(0,0,0,.12)}
.about-photo{left:147px;top:1069px;width:446px;height:446px;background:radial-gradient(circle at 55% 40%,#e8c7a4,#b98a63 50%,#6f5a4d 100%)}
.h2{font-weight:700;color:var(--brown);font-size:38px;line-height:1.2}
.kicker{font-size:13px;font-weight:600;color:var(--ink)}
.body{font-size:13.5px;line-height:22px;color:var(--muted);font-weight:300}
.btn-dark{display:inline-block;background:var(--btn);color:var(--white);border-radius:22px;font-size:12px;font-weight:700;text-align:center}

/* services */
.center{position:absolute;left:0;width:1200px;text-align:center}
.card{position:absolute;width:327px;height:186px;background:var(--card);border-radius:22px;overflow:hidden}
.card h3{position:absolute;left:28px;top:26px;font-size:17px;font-weight:600;color:var(--ink)}
.card p{position:absolute;left:28px;top:57px;font-size:13px;line-height:20px;color:var(--muted)}
.card .go{position:absolute;left:28px;top:118px;width:24px;height:24px;border-radius:50%;background:var(--white);display:flex;align-items:center;justify-content:center}
.card svg.ic{position:absolute;right:40px;bottom:-4px}

/* app banner */
.app{position:absolute;left:89px;top:2741px;width:1022px;height:354px;background:var(--green);border-radius:32px}
.app-visual{position:absolute;left:150px;top:2681px;width:290px;height:414px;background:linear-gradient(160deg,#f3f1e8 0,#e8d3bf 55%,#c79f81 100%);border-radius:30px 30px 0 0;opacity:.95}
.store{position:absolute;top:2967px;height:48px;background:var(--white);border-radius:24px;display:flex;align-items:center;gap:10px;padding-left:18px;color:#111}
.store .mk{width:20px;height:20px;border-radius:50%;background:var(--ink)}
.store small{display:block;font-size:7.5px;line-height:1}
.store b{display:block;font-size:15px;font-weight:500;line-height:1.2}

/* news */
.news-img{position:absolute;top:3262px;width:239px;height:191px;border-radius:20px}
.news-date{position:absolute;top:3480px;font-size:10px;font-weight:600;color:#b9c21c}
.news-title{position:absolute;top:3504px;font-size:15px;line-height:21px;font-weight:600;color:var(--ink)}
.news-btn{position:absolute;top:3565px;width:94px;height:28px;line-height:28px;font-size:11px}
.vline{position:absolute;top:3262px;width:1px;height:336px;background:var(--line)}

/* footer */
.footer{position:absolute;top:3677px;left:0;width:1200px;height:481px;background:#fafafa;border-top:1px solid var(--line)}
.fh{position:absolute;font-size:16px;font-weight:600;color:var(--brown)}
.ft{position:absolute;font-size:12.5px;line-height:22px;color:var(--muted)}
.fdate{position:absolute;font-size:11.5px;font-weight:600;color:#b9c21c}
.hr{position:absolute;height:1px;background:var(--line)}
.input{position:absolute;left:854px;top:3795px;width:257px;height:45px;border-radius:23px;background:#ecebea;padding-left:30px;line-height:45px;font-size:12.5px;color:var(--muted)}
.send{position:absolute;left:854px;top:3852px;width:257px;height:45px;border-radius:23px;background:var(--green);color:var(--white);text-align:center;line-height:45px;font-weight:700;font-size:15px}
.totop{position:absolute;left:1137px;top:4069px;width:38px;height:38px;border-radius:50%;background:var(--btn);display:flex;align-items:center;justify-content:center}
.copy{position:absolute;top:4114px;left:0;width:1200px;text-align:center;font-size:12.5px;font-weight:500;color:var(--ink)}
</style>
</head>
<body>
<div class="page">

<header class="header">
  <div class="brand"><span class="dot"></span>Laanemetsa Haldusgrupp</div>
  <nav class="nav">
    <div class="lang"><span class="flag"></span>ES ⌄</div>
    <div>KLIENDITUGI</div>
    <div class="btn-pill">SISENE E-TEENINDUSSE</div>
    <div class="burger"><span></span><span></span><span></span></div>
  </nav>
</header>

<section class="hero">
  <div class="hero-photo" role="img" aria-label="Smiling senior woman hiking in an autumn forest"></div>
  <svg width="1200" height="714" viewBox="0 0 1200 714"><path d="M0 0H662C640 260 470 560 0 690Z" fill="#aba39e"/></svg>
  <div class="hero-kicker">TERE TULEMAST</div>
  <div class="hero-title">Laanemetsa</div>
  <div class="hero-sub">Haldusgrupp</div>
</section>

<section class="quick">
  <div class="quick-item" style="left:205px">
    <svg width="80" height="80" viewBox="0 0 80 80" fill="none" stroke="#6e6560" stroke-width="2"><circle cx="36" cy="38" r="28"/><ellipse cx="36" cy="38" rx="12" ry="28"/><path d="M8 38h56M12 24h48M12 52h48"/><path d="M50 70c2-16 12-24 24-26-2 14-10 24-24 26z" fill="#d3dc2c" stroke="#6e6560"/></svg>
    Keskkond, kvaliteet</div>
  <div class="quick-item" style="left:415px">
    <svg width="80" height="80" viewBox="0 0 80 80" fill="none" stroke="#6e6560" stroke-width="2"><circle cx="40" cy="40" r="32"/><path d="M30 46l-6-10 6-10M50 34l6 10-6 10M32 26h16"/><path d="M34 44l6-8 6 8h-12z" stroke="#c3cb1f"/></svg>
    Tule tööle!</div>
  <div class="quick-item" style="left:576px">
    <svg width="80" height="80" viewBox="0 0 80 80" fill="none" stroke="#6e6560" stroke-width="2"><rect x="16" y="10" width="50" height="62" rx="3"/><rect x="10" y="22" width="10" height="50" rx="3"/><path d="M26 22h14M26 32h14M26 42h34M26 52h34M26 62h34" stroke="#c3cb1f"/><rect x="46" y="20" width="14" height="14"/></svg>
    Uudised</div>
  <div class="quick-item" style="left:775px">
    <svg width="80" height="80" viewBox="0 0 80 80" fill="none" stroke="#6e6560" stroke-width="2"><rect x="26" y="8" width="28" height="22" rx="2" fill="#eef1a8"/><path d="M8 40l14-8 16 6 10-4 24 8M8 40l14 22M72 42L58 62M22 62l10 6 8-4 10 4 8-6"/><path d="M30 48l8 8M36 44l10 10"/></svg>
    Hanked ja toetused</div>
</section>

<section>
  <div class="round-photo about-photo" role="img" aria-label="Young woman with wind in her hair by a lake at sunset"></div>
  <h2 class="h2 abs" style="left:647px;top:1122px">Ettevõttest</h2>
  <div class="kicker abs" style="left:648px;top:1170px">Laanemetsa Haldusgrupp</div>
  <p class="body abs" style="left:648px;top:1207px;width:412px">Laanemetsa Haldusgrupp on Eesti juhtiv jäätmekäitlus- ja kommunaalteenuseid pakkuv kontsern, mille põhitegevuseks on olmejäätmete kogumine. Lisaks sellele tegeleb ettevõte teisese toorme, ehitusjäätmete ning muude jäätmete kogumisega. Mõningates piirkondades pakub ettevõte talvisel ajal ka teede ja tänavate hooldusteenust. Ettevõte teenindab Eestis enam kui 100 000 klienti ning käitleb üle 250 000 tonni jäätmeid aastas. Kontsern annab tööd ligi 600 inimesele ja selle käive ületas 2016.</p>
  <div class="btn-dark abs" style="left:651px;top:1439px;width:129px;height:42px;line-height:42px">LOE VEEL</div>
</section>

<section>
  <h2 class="h2 center" style="top:1595px">Our Services in<br>Laanemetsa Haldusgrupp</h2>

  <div class="card" style="left:89px;top:1725px"><h3>Teenused Ärikliendile</h3><p>Laanemetsa Haldusgrupp<br>on Eesti juhtiv...</p><span class="go"><svg width="8" height="8" viewBox="0 0 8 8"><path d="M3 1l3 3-3 3" stroke="#6e6560" fill="none"/></svg></span>
    <svg class="ic" width="90" height="82" viewBox="0 0 90 82" fill="none" stroke="#6e6560" stroke-width="2"><circle cx="45" cy="44" r="40"/><ellipse cx="45" cy="44" rx="16" ry="40"/><path d="M5 44h80M10 26h70M10 62h70"/><circle cx="45" cy="52" r="8" stroke="#c3cb1f"/><path d="M30 82c2-12 28-12 30 0" stroke="#c3cb1f"/></svg></div>
  <div class="card" style="left:436px;top:1725px"><h3>Teenused Erakliendile</h3><p>Laanemetsa Haldusgrupp<br>on Eesti juhtiv...</p><span class="go"><svg width="8" height="8" viewBox="0 0 8 8"><path d="M3 1l3 3-3 3" stroke="#6e6560" fill="none"/></svg></span>
    <svg class="ic" width="90" height="82" viewBox="0 0 90 82" fill="none" stroke="#6e6560" stroke-width="2"><circle cx="45" cy="14" r="8"/><circle cx="22" cy="44" r="8"/><circle cx="68" cy="44" r="8"/><circle cx="45" cy="50" r="8" stroke="#c3cb1f"/><path d="M8 80c0-14 28-14 28 0M54 80c0-14 28-14 28 0M31 82c0-14 28-14 28 0M33 36c0-10 24-10 24 0"/></svg></div>
  <div class="card" style="left:783px;top:1725px"><h3>Jäätmejaamad</h3><p>Laanemetsa Haldusgrupp<br>on Eesti juhtiv...</p><span class="go"><svg width="8" height="8" viewBox="0 0 8 8"><path d="M3 1l3 3-3 3" stroke="#6e6560" fill="none"/></svg></span>
    <svg class="ic" width="90" height="82" viewBox="0 0 90 82" fill="none" stroke="#6e6560" stroke-width="2"><path d="M14 50A32 32 0 0 1 70 18M76 36A32 32 0 0 1 24 76"/><path d="M64 10l8 8-10 4M26 82l-4-10 10-2"/><path d="M32 34h26l-4 36H36z" stroke="#c3cb1f"/><path d="M30 34h30M40 28h10"/></svg></div>
  <div class="card" style="left:89px;top:1932px"><h3>Teed ja tänavad</h3><p>Laanemetsa Haldusgrupp<br>on Eesti juhtiv...</p><span class="go"><svg width="8" height="8" viewBox="0 0 8 8"><path d="M3 1l3 3-3 3" stroke="#6e6560" fill="none"/></svg></span>
    <svg class="ic" width="90" height="82" viewBox="0 0 90 82" fill="none" stroke="#6e6560" stroke-width="2"><rect x="10" y="34" width="22" height="30"/><rect x="32" y="14" width="20" height="50" stroke="#c3cb1f"/><rect x="52" y="24" width="26" height="40"/><path d="M2 64h86M4 80h8M20 80h8M36 80h8M52 80h8M68 80h8M16 42h10M16 52h10M58 34h14M58 44h14M58 54h14"/></svg></div>
  <div class="card" style="left:436px;top:1932px"><h3>Korraldatud jäätmevedu</h3><p>Laanemetsa Haldusgrupp<br>on Eesti juhtiv...</p><span class="go"><svg width="8" height="8" viewBox="0 0 8 8"><path d="M3 1l3 3-3 3" stroke="#6e6560" fill="none"/></svg></span>
    <svg class="ic" width="110" height="82" viewBox="0 0 110 82" fill="none" stroke="#6e6560" stroke-width="2"><rect x="6" y="10" width="44" height="40" rx="4" transform="rotate(-15 28 30)" fill="#eef1a8" stroke="#c3cb1f"/><path d="M10 58h60V40h20l12 14v12H10z"/><circle cx="26" cy="70" r="7"/><circle cx="84" cy="70" r="7"/></svg></div>
</section>

<section>
  <div class="brand" style="left:165px;top:2280px;font-size:18px"><span class="dot" style="width:52px;height:52px"></span>Laanemetsa<br>Haldusgrupp</div>
  <h2 class="h2 abs" style="left:165px;top:2355px">Tule Tööle!</h2>
  <div class="kicker abs" style="left:165px;top:2402px">Laanemetsa Haldusgrupp</div>
  <p class="body abs" style="left:165px;top:2441px;width:420px">Ootame oma meeskonda tubilsid ja töökaid inimesi.<br>Meie ettevõttesse saab kandideerida läbi CV keskuse</p>
  <div class="abs" style="left:165px;top:2498px;font-size:19px;font-weight:700;color:var(--brown);text-decoration:underline;text-underline-offset:5px">vaata kõiki aktiivseid töökuulutusi.</div>
  <div class="round-photo" role="img" aria-label="Volunteers in green shirts collecting litter in a park" style="left:589px;top:2193px;width:446px;height:446px;background:radial-gradient(circle at 50% 45%,#a8b68a,#5d8a3c 55%,#3c5a2a 100%)"></div>
</section>

<section>
  <div class="app"></div>
  <div class="app-visual" role="img" aria-label="Hand holding a smartphone showing the mobile app"></div>
  <h2 class="abs" style="left:638px;top:2812px;font-size:38px;line-height:40px;font-weight:700;color:var(--white)">Laadige alla meie<br>rakendused</h2>
  <div class="abs" style="left:638px;top:2911px;font-size:20px;font-weight:700;color:var(--white)">Saadaval Nimbus- ja Kairo-seadmetes.</div>
  <div class="store" style="left:640px;width:171px"><span class="mk"></span><span><small>GET IN ON</small><b>AppVault</b></span></div>
  <div class="store" style="left:820px;width:172px"><span class="mk"></span><span><small>DOWNLOAD ON THE</small><b>PlayDepot</b></span></div>
</section>

<section>
  <h2 class="h2 center" style="top:3180px">Viimased Uudised:</h2>
  <div class="news-img" role="img" aria-label="Wooden boardwalk through a misty bog at sunrise" style="left:178px;background:linear-gradient(180deg,#d9cfc0,#a89a7d 60%,#6f6048)"></div>
  <div class="news-img" role="img" aria-label="Close-up of a pine branch with needles" style="left:481px;background:radial-gradient(circle,#f1eee8,#b9ad99 60%,#8c7f6d)"></div>
  <div class="news-img" role="img" aria-label="Laughing child" style="left:783px;background:linear-gradient(160deg,#6a5a4b,#c99f7d 55%,#e9d7c6)"></div>
  <div class="vline" style="left:449px"></div>
  <div class="vline" style="left:751px"></div>
  <div class="news-date" style="left:178px">14.12.2023</div>
  <div class="news-date" style="left:481px">01.01.2024</div>
  <div class="news-date" style="left:783px">16.12.2016</div>
  <div class="news-title" style="left:178px">Tallinna klienditeeninduse<br>lahtiolekuaegade muudatus</div>
  <div class="news-title" style="left:481px">Käibemaksumäära<br>muudatus alates</div>
  <div class="news-title" style="left:783px">Arvete koostamise<br>muudatused</div>
  <div class="btn-dark news-btn" style="left:183px">Loe veel</div>
  <div class="btn-dark news-btn" style="left:481px">Loe veel</div>
  <div class="btn-dark news-btn" style="left:783px">Loe veel</div>
</section>

<footer>
  <div class="footer"></div>
  <div class="brand" style="left:89px;top:3760px;font-size:16px"><span class="dot" style="width:56px;height:56px"></span>Laanemetsa<br>Haldusgrupp</div>
  <div class="ft" style="left:87px;top:3864px;line-height:17px">AS Laanemetsa Haldusgrupp<br>Kuusiku 8, Tallinn 10412</div>
  <div class="hr" style="left:87px;top:3906px;width:190px"></div>
  <div class="ft" style="left:87px;top:3915px">Registrikood: 10455931</div>
  <div class="hr" style="left:87px;top:3944px;width:190px"></div>
  <div class="ft" style="left:87px;top:3952px">Tel. (+372) 600 12 34</div>

  <div class="fh" style="left:363px;top:3744px">Erakorralised Teated</div>
  <div class="fdate" style="left:363px;top:3789px">14.12.2024</div>
  <div class="ft" style="left:363px;top:3810px">Alates 01.01.2024 on Tallinna<br>klienditeenindus (Kuusiku 8,</div>
  <div class="hr" style="left:363px;top:3866px;width:225px"></div>
  <div class="fdate" style="left:363px;top:3884px">10-05-2022</div>
  <div class="ft" style="left:363px;top:3905px">Klienditeenindus Viljandis avatud<br>ühel päeval nädalas - reedel.</div>
  <div class="ft" style="left:363px;top:3972px;font-weight:600;color:var(--brown);text-decoration:underline">Teenindamata aadressid</div>

  <div class="fh" style="left:673px;top:3744px">Kiirlingid</div>
  <div class="ft" style="left:673px;top:3790px;line-height:31.5px">Avaleht<br>Kodukliendile<br>Ärikliendile<br>Klienditugi<br>Ettevõttest<br>Tule tööle!</div>
  <div class="ft" style="left:673px;top:3979px">Isikuandmete töötlemise<br>üldtingimused</div>

  <div class="fh" style="left:854px;top:3744px">Vaata Järgmist Veopäeva</div>
  <div class="input">Lepingu nr.:</div>
  <div class="send">VAATA</div>

  <div class="totop"><svg width="10" height="8" viewBox="0 0 10 8"><path d="M1 6l4-4 4 4" stroke="#fff" fill="none" stroke-width="1.5"/></svg></div>
  <div class="hr" style="left:89px;top:4089px;width:1022px"></div>
  <div class="copy">© Autoriõigus 2024 Laanemetsa Haldusgrupp, Kõik õigused kaitstud</div>
</footer>

</div>
</body>
</html>
```